Business Card Design

Business Card for professional consulting firm working with large financial institutions.

Target Market(s)

Executive buyers

Industry/Entity Type

Banking

Contact Information for Business Card

Mild creativity wanted. Not boring, but do elaborate artwork.

Font styles to use
Serif
Sans Serif

Colors

Designer to choose colors to be used in the design.

Requirements
Must have
• Standard business card features - company name, individual name, telephone, website, email, locations.
Nice to have
• Two colors
Should not have
• too many colors, fancy printing, cartoons.

```html
<!DOCTYPE html>
<html lang="en">
<head>
<meta charset="utf-8">
<title>Kestrel Group – Business Card</title>
<link rel="stylesheet" href="https://fonts.googleapis.com/css2?family=Merriweather:wght@400&family=Roboto:wght@400;500;700&display=swap">
<style>
  :root {
    --backdrop: #ecebe8;
    --card-white: #f4f4f4;
    --card-black: #050505;
    --card-dark: #1b1d20;
    --ink: #111111;
    --ink-soft: #555555;
    --ink-muted: #a5a5a5;
    --logo-grey: #3a3a3a;
    --arc-grey: #c8c8c8;
    --band-grey: #c4c4c4;
    --white: #ffffff;
  }
  * { margin: 0; padding: 0; box-sizing: border-box; }
  html, body { width: 1200px; height: 960px; overflow: hidden; }
  body {
    background: var(--backdrop);
    position: relative;
    font-family: "Roboto", Arial, sans-serif;
  }
  .card {
    position: absolute;
    width: 600px;
    height: 343px;
    overflow: hidden;
    box-shadow: 0 3px 8px rgba(0,0,0,0.25);
  }
  .card-front { left: 314px; top: 113px; background: var(--card-black); }
  .card-back  { left: 311px; top: 472px; background: var(--card-dark); }

  .front-shape { position: absolute; inset: 0; }

  .brand-name {
    position: absolute;
    font-family: "Merriweather", Georgia, serif;
    font-weight: 400;
    white-space: nowrap;
  }
  .card-front .brand-name {
    left: 44px; width: 260px; top: 150px;
    text-align: center;
    font-size: 26px;
    color: var(--logo-grey);
  }
  .card-back .brand-name {
    left: 0; right: 0; top: 142px;
    text-align: center;
    font-size: 30px;
    color: var(--white);
  }

  .divider {
    position: absolute;
    left: 335px; top: 92px;
    width: 1px; height: 160px;
    background: #d6d6d6;
  }
  .contact {
    position: absolute;
    left: 366px; top: 92px;
    color: var(--ink-soft);
  }
  .person-name {
    font-size: 20px; font-weight: 700;
    color: var(--ink); letter-spacing: 0.3px;
    line-height: 24px;
  }
  .person-title {
    font-size: 15px; font-weight: 500;
    color: var(--ink-muted);
    line-height: 18px;
  }
  .address {
    margin-top: 14px;
    font-size: 14.5px; line-height: 19px;
    font-style: normal;
  }
  .contact-list { list-style: none; margin-top: 10px; }
  .contact-list li {
    display: flex; align-items: center; gap: 8px;
    font-size: 14.5px; line-height: 19.5px;
  }
  .contact-list svg { width: 13px; height: 13px; fill: var(--ink); flex: none; }

  .web-band {
    position: absolute;
    left: 0; right: 0; top: 275px; height: 29px;
    background: var(--band-grey);
    color: var(--white);
    font-size: 14px;
    letter-spacing: 6px;
    text-align: center;
    line-height: 29px;
  }
</style>
</head>
<body>
  <section class="card card-front" aria-label="Card front">
    <svg class="front-shape" viewBox="0 0 600 343" width="600" height="343" aria-hidden="true">
      <path d="M0,0 H465 Q585,35 600,150 V343 H132 Q25,320 0,205 Z" fill="var(--card-white)"/>
      <path d="M468,0 Q588,35 600,150" fill="none" stroke="var(--arc-grey)" stroke-width="5"/>
      <path d="M4,212 Q30,318 132,341" fill="none" stroke="var(--arc-grey)" stroke-width="5"/>
    </svg>
    <div class="brand-name">Kestrel Group</div>
    <div class="divider"></div>
    <div class="contact">
      <h1 class="person-name">DANIEL MARSH</h1>
      <p class="person-title">CEO/FOUNDER</p>
      <address class="address">4210 Larkspur Court<br>Fairbanks, Alaska 36218</address>
      <ul class="contact-list">
        <li><svg viewBox="0 0 24 24"><path d="M6.6 10.8a15.2 15.2 0 0 0 6.6 6.6l2.2-2.2a1 1 0 0 1 1-.25 11.4 11.4 0 0 0 3.6.57 1 1 0 0 1 1 1V20a1 1 0 0 1-1 1A17 17 0 0 1 3 4a1 1 0 0 1 1-1h3.5a1 1 0 0 1 1 1c0 1.25.2 2.45.57 3.57a1 1 0 0 1-.25 1z"/></svg>555 210 4871</li>
        <li><svg viewBox="0 0 24 24"><path d="M2 5h20v14H2z"/><path d="M3 6.5l9 7 9-7" fill="none" stroke="var(--card-white)" stroke-width="1.6"/></svg>info@kestrelgroup.com</li>
        <li><svg viewBox="0 0 24 24"><circle cx="12" cy="12" r="10"/><path d="M7 8c2 0 3 1 3 3s-2 2-2 4M14 4c0 2 2 3 3 3s2 2 1 4" fill="none" stroke="var(--card-white)" stroke-width="1.6"/></svg>www.kestrelgroup.com</li>
      </ul>
    </div>
  </section>

  <section class="card card-back" aria-label="Card back">
    <div class="brand-name">Kestrel Group</div>
    <div class="web-band">www.kestrelgroup.com</div>
  </section>
</body>
</html>
```